Looking for a modern, Professional business card design

We have a simple business card, but are looking for a more modern, professional look. A sample of the basic card is attached as well as the logo. We would also like to add that we offer:
Struggling with your finances?
- Learn to become debt free
- Discover the power of cash
- Control your money instead of it controlling you
Let us help you achieve a new level of financial freedom!
Also, we would like to have a "SPECIAL OFFER!: FREE 30 minute consultation"
Financial Planning

```html
<!DOCTYPE html>
<html lang="en">
<head>
<meta charset="utf-8">
<title>Harbor Lane Money Coaching – Business Card</title>
<link rel="stylesheet" href="https://fonts.googleapis.com/css2?family=Roboto+Condensed:wght@300;400;700&family=Roboto:wght@300;400&display=swap">
<style>
  :root {
    --stage: #d8d5cf;
    --card-light: #eceeeb;
    --card-dark: #0d0d0d;
    --green: #3c9a2e;
    --green-muted: #3f8a34;
    --ink: #1e1e1e;
    --text-light: #f2f2f2;
    --text-soft: #d9d9d9;
    --accent-rose: #f3c9c4;
  }
  html, body {
    margin: 0;
    padding: 0;
    width: 1200px;
    height: 969px;
    overflow: hidden;
    background: var(--stage);
  }
  .card {
    position: absolute;
    left: 50px;
    top: 171px;
    width: 1100px;
    height: 626px;
    border-radius: 30px;
    overflow: hidden;
    background: var(--card-light);
    font-family: "Roboto", Arial, sans-serif;
    box-shadow: 0 6px 24px rgba(0,0,0,0.18);
  }
  .card-shape {
    position: absolute;
    inset: 0;
  }
  .brand {
    position: absolute;
    left: 48px;
    top: 78px;
    display: flex;
    align-items: center;
    gap: 18px;
  }
  .brand-dot {
    width: 54px;
    height: 54px;
    border-radius: 50%;
    background: var(--green);
    flex: none;
  }
  .brand-name {
    font-family: "Roboto Condensed", Arial, sans-serif;
    font-weight: 700;
    font-size: 46px;
    line-height: 1.0;
    color: var(--ink);
    text-transform: uppercase;
    letter-spacing: 0.5px;
  }
  .contact {
    position: absolute;
    right: 51px;
    text-align: right;
    color: var(--text-light);
  }
  .person-name {
    top: 84px;
    margin: 0;
    font-family: "Roboto Condensed", Arial, sans-serif;
    font-weight: 400;
    font-size: 36px;
    letter-spacing: 1px;
    color: var(--green);
  }
  .person-role {
    top: 130px;
    font-weight: 300;
    font-size: 29px;
    color: var(--text-soft);
  }
  .details {
    top: 198px;
    list-style: none;
    margin: 0;
    padding: 0;
    font-size: 26px;
    font-weight: 300;
    line-height: 42px;
  }
  .details li {
    display: flex;
    justify-content: flex-end;
    align-items: center;
    gap: 18px;
  }
  .details svg {
    width: 24px;
    height: 24px;
    flex: none;
  }
  .pitch {
    top: 340px;
    font-family: "Roboto Condensed", Arial, sans-serif;
  }
  .pitch-question {
    margin: 0;
    font-size: 30px;
    font-weight: 400;
    color: var(--green);
    letter-spacing: 0.5px;
  }
  .pitch-points {
    margin: 4px 0 0;
    font-family: "Roboto", Arial, sans-serif;
    font-weight: 300;
    font-size: 25px;
    line-height: 38px;
    color: var(--text-light);
  }
  .pitch-points .sep {
    color: var(--green);
  }
  .pitch-promise {
    margin: 18px 0 0;
    font-size: 24px;
    font-weight: 400;
    color: var(--accent-rose);
  }
  .pitch-offer {
    margin: 8px 0 0;
    font-size: 30px;
    font-weight: 400;
    color: var(--green-muted);
    letter-spacing: 0.5px;
  }
</style>
</head>
<body>
  <div class="card">
    <svg class="card-shape" viewBox="0 0 1100 626" width="1100" height="626" aria-hidden="true">
      <defs>
        <linearGradient id="swoosh" x1="0" y1="0" x2="0" y2="1">
          <stop offset="0" stop-color="#5aa84a" stop-opacity="0.9"/>
          <stop offset="1" stop-color="#9aa59a" stop-opacity="0.2"/>
        </linearGradient>
      </defs>
      <path d="M 745 0 C 660 140, 500 220, 400 320 C 320 400, 270 500, 240 626 L 275 626 C 320 500, 370 410, 450 330 C 560 220, 720 140, 806 0 Z" fill="url(#swoosh)"/>
      <path d="M 806 0 L 1100 0 L 1100 626 L 275 626 C 320 500, 370 410, 450 330 C 560 220, 720 140, 806 0 Z" fill="var(--card-dark)"/>
    </svg>

    <div class="brand">
      <span class="brand-dot"></span>
      <span class="brand-name">Harbor Lane<br>Money Coaching</span>
    </div>

    <h1 class="contact person-name">DANIEL R. WHITFIELD</h1>
    <div class="contact person-role">Personal Financial Coach</div>

    <ul class="contact details">
      <li>(205) 555-0187
        <svg viewBox="0 0 24 24"><rect x="6" y="2" width="12" height="20" rx="2" fill="none" stroke="var(--green)" stroke-width="2"/><line x1="10" y1="18" x2="14" y2="18" stroke="var(--green)" stroke-width="2"/></svg>
      </li>
      <li>daniel@steadyledgerhome.com
        <svg viewBox="0 0 24 24"><rect x="2" y="5" width="20" height="14" fill="var(--green)"/><path d="M2 5 L12 13 L22 5" fill="none" stroke="var(--card-dark)" stroke-width="1.8"/></svg>
      </li>
      <li>www.steadyledgerhome.com
        <svg viewBox="0 0 24 24"><circle cx="12" cy="12" r="10" fill="var(--green)"/><path d="M7 8 Q10 6 11 9 Q9 12 12 14 Q14 17 11 20 M15 5 Q17 9 19 10" fill="none" stroke="var(--card-dark)" stroke-width="1.6"/></svg>
      </li>
    </ul>

    <div class="contact pitch">
      <p class="pitch-question">STRUGGLING WITH YOUR FINANCES?</p>
      <p class="pitch-points">Learn to become debt free <span class="sep">•</span> Discover the power of cash<br>Control your money instead of it controlling you</p>
      <p class="pitch-promise">LET US HELP YOU ACHIEVE A NEW LEVEL OF FINANCIAL FREEDOM!</p>
      <p class="pitch-offer">SPECIAL OFFER!: FREE 30 MINUTE CONSULTATION</p>
    </div>
  </div>
</body>
</html>
```